Locksmith Business Cards

My father-in-law is in need of new business cards for his locksmith business and I need to impress him. Kindly help me out!

You can see the previous business card attached. It is a family run business in North Wales.

No individual names on the cards.

Key Things to Feature:
- The words "Prompt", "Local", "Reliable" (as you can see under the logo on the website)
- 24h Emergency Service
- Covering All of North Wales, the Wirral and Chester
- The color blue
- A key or a lock would be interesting (similar to the ones that come up when you google locksmith business card)

Optional (only if design includes bullet points, like the example below):
https://imgvaultcdn.net/samples/208314/55172/55172_3904821_208314_image.jpg
- Residential / Commercial / Automotive
- Alarms & Cameras
- Key Cutting & Safes

https://www.brynhafod-locksmiths.co.uk/

Industry/Entity Type

Locksmith

Contact Information for Business Card

01632 960 418
07700 900 362
brynhafodlocksmiths@mailvane.com
Brynhafod Locksmiths, The Willow Barn, 7 Tannery Rd., Llandudno LL99 4QX
www.brynhafod-locksmiths.co.uk

Requirements
Must have
• - The words "Prompt", "Local", "Reliable" (as you can see under the logo on the website)
• - 24h Emergency Service
• - Covering All of North Wales, the Wirral and Chester
Nice to have
• - A key or a lock would be interesting (similar to the ones that come up when you google locksmith business card)

```html
<!DOCTYPE html>
<html lang="en">
<head>
<meta charset="utf-8">
<title>Brynhafod Locksmiths – Business Card</title>
<link href="https://fonts.googleapis.com/css2?family=Oswald:wght@500;700&family=Source+Sans+3:wght@400;600&display=swap" rel="stylesheet">
<style>
  :root {
    --navy: #1e2a6b;
    --royal: #283f8a;
    --accent: #3f55a5;
    --grey: #979797;
    --white: #ffffff;
    --page: #e8e9ed;
  }
  * { margin: 0; padding: 0; box-sizing: border-box; }
  html, body { width: 1200px; height: 848px; overflow: hidden; }
  body {
    background: var(--page);
    font-family: "Source Sans 3", sans-serif;
    position: relative;
  }
  .card {
    position: absolute;
    left: 330px;
    width: 540px;
    height: 356px;
    background: var(--white);
    overflow: hidden;
  }
  .card--front { top: 40px; }
  .card--back { top: 452px; }

  /* Brand lockup */
  .brand { display: flex; align-items: center; gap: 14px; }
  .brand__mark {
    background: var(--navy);
    border-radius: 12px;
    flex: none;
  }
  .brand__name {
    font-family: "Oswald", sans-serif;
    font-weight: 500;
    color: var(--navy);
    text-transform: uppercase;
    line-height: 0.98;
    letter-spacing: -0.5px;
  }

  /* Front */
  .front__brand {
    position: absolute;
    top: 95px;
    left: 0; right: 0;
    justify-content: center;
  }
  .front__brand .brand__mark { width: 72px; height: 86px; }
  .front__brand .brand__name { font-size: 50px; }
  .tagline {
    position: absolute;
    top: 252px;
    left: 0; right: 0;
    text-align: center;
    font-weight: 600;
    font-size: 18px;
    color: var(--navy);
    word-spacing: 4px;
  }
  .emergency-band {
    position: absolute;
    left: 0; right: 0; bottom: 0;
    height: 71px;
    background: var(--royal);
    color: var(--white);
    text-align: center;
    padding-top: 7px;
  }
  .emergency-band__title {
    font-weight: 600;
    font-size: 25px;
    line-height: 1.1;
    letter-spacing: 0.3px;
  }
  .emergency-band__hours {
    font-family: "Oswald", sans-serif;
    font-weight: 700;
    font-size: 29px;
    margin-right: 8px;
    letter-spacing: -1px;
  }
  .emergency-band__coverage {
    font-size: 16px;
    line-height: 1.2;
  }

  /* Back */
  .side-strip {
    position: absolute;
    left: 0; top: 0; bottom: 0;
    width: 70px;
    background: var(--royal);
  }
  .side-strip__dot {
    position: absolute;
    left: 13px;
    top: 148px;
    width: 44px;
    height: 44px;
    border-radius: 50%;
    background: var(--white);
  }
  .back__brand {
    position: absolute;
    top: 33px;
    left: 106px;
    gap: 10px;
  }
  .back__brand .brand__mark { width: 42px; height: 54px; border-radius: 8px; }
  .back__brand .brand__name { font-size: 31px; }
  .contact-list {
    position: absolute;
    top: 127px;
    left: 112px;
    list-style: none;
  }
  .contact-list__item {
    display: flex;
    align-items: center;
    height: 31px;
    color: var(--grey);
    font-size: 18px;
  }
  .contact-list__icon {
    width: 24px;
    height: 24px;
    margin-right: 23px;
    flex: none;
  }
  .contact-list__sep { color: var(--navy); margin: 0 10px; }
  .services {
    position: absolute;
    top: 281px;
    left: 117px;
    font-weight: 600;
    font-size: 16.5px;
    line-height: 21px;
    text-transform: uppercase;
  }
  .services__alt { color: var(--accent); }
  .services__main { color: var(--navy); }
</style>
</head>
<body>

<section class="card card--front" aria-label="Business card front">
  <div class="brand front__brand">
    <span class="brand__mark"></span>
    <div class="brand__name">Brynhafod<br>Locksmiths</div>
  </div>
  <p class="tagline">Prompt. Local. Reliable</p>
  <div class="emergency-band">
    <p class="emergency-band__title"><span class="emergency-band__hours">24/7</span>EMERGENCY SERVICE</p>
    <p class="emergency-band__coverage">Covering All of North Wales, the Wirral and Chester</p>
  </div>
</section>

<section class="card card--back" aria-label="Business card back">
  <div class="side-strip"><span class="side-strip__dot"></span></div>

  <div class="brand back__brand">
    <span class="brand__mark"></span>
    <div class="brand__name">Brynhafod<br>Locksmiths</div>
  </div>

  <ul class="contact-list">
    <li class="contact-list__item">
      <svg class="contact-list__icon" viewBox="0 0 24 24" fill="none" stroke="#283f8a" stroke-width="1.6"><rect x="2" y="5" width="20" height="14"/><path d="M2 5l10 8 10-8M2 19l7.5-7.5M22 19l-7.5-7.5"/></svg>
      brynhafodlocksmiths@mailvane.com
    </li>
    <li class="contact-list__item">
      <svg class="contact-list__icon" viewBox="0 0 24 24" fill="#283f8a"><path d="M6.6 2.5l3 3.6-1.8 2.2c1.2 2.8 3.2 4.9 6 6.2l2.2-1.8 3.6 3-2 3c-7.6-.4-13.6-6.5-14-14z"/></svg>
      01632 960 418<span class="contact-list__sep">/</span>07700 900 362
    </li>
    <li class="contact-list__item">
      <svg class="contact-list__icon" viewBox="0 0 24 24" fill="none" stroke="#283f8a" stroke-width="1.3"><circle cx="12" cy="12" r="10"/><ellipse cx="12" cy="12" rx="4.5" ry="10"/><path d="M2 12h20M4 6.5h16M4 17.5h16M12 2v20"/></svg>
      www.brynhafod-locksmiths.co.uk
    </li>
    <li class="contact-list__item">
      <svg class="contact-list__icon" viewBox="0 0 24 24" fill="#283f8a"><path d="M12 1.5a7 7 0 0 0-7 7c0 5 7 14 7 14s7-9 7-14a7 7 0 0 0-7-7zm0 10a3 3 0 1 1 0-6 3 3 0 0 1 0 6z"/></svg>
      7 Tannery Rd, Llandudno LL99 4QX
    </li>
  </ul>

  <p class="services">
    <span class="services__alt">Residential &amp; Commercial</span> <span class="services__main">- Automotive</span><br>
    <span class="services__main">Alarms &amp; Cameras</span> <span class="services__alt">- Key Cutting &amp; Safes</span>
  </p>
</section>

</body>
</html>
```